Business Card Design for Occupational Medicine Start Up Company

We need to design a professional business card. We are a healthcare company providing occupational medicine services to blue collar industries. We are professional, efficient and high quality service providers.

Target Market(s)

Blue Collar Industry: Shipbuilding, Ports, Trucking Companies; The Executives and Safety Officers for these companies

Industry/Entity Type

Healthcare

Contact Information for Business Card

Logo, Name, Title, Email, Phone

Other font styles liked:
• Please match our Brand Guide

Requirements
Must have
• Our Company Colors and Logo

```html
<!DOCTYPE html>
<html lang="en">
<head>
<meta charset="utf-8">
<title>CrewSafe Clinics – Business Card</title>
<link href="https://fonts.googleapis.com/css2?family=Montserrat:wght@600;700&family=Questrial&display=swap" rel="stylesheet">
<style>
  :root {
    --page-bg: #2b2b2d;
    --card-bg: #1b1c1e;
    --band: #85878a;
    --white: #ffffff;
    --muted: #8e9094;
    --shadow: rgba(0,0,0,0.55);
  }
  * { box-sizing: border-box; margin: 0; padding: 0; }
  html, body {
    width: 1200px; height: 1024px; overflow: hidden;
    background: var(--page-bg);
  }
  .card {
    position: absolute;
    left: 230px;
    width: 740px; height: 423px;
    background: var(--card-bg);
    box-shadow: 0 14px 30px var(--shadow);
    overflow: hidden;
  }
  .card--front { top: 60px; }
  .card--back  { top: 541px; }

  .brand {
    font-family: "Montserrat", sans-serif;
    font-weight: 600;
    color: var(--white);
    text-transform: uppercase;
    line-height: 1;
  }
  .brand__line { display: block; }
  .brand__sub { letter-spacing: 0.45em; }

  /* front */
  .front-lockup {
    position: absolute; inset: 0;
    display: flex; flex-direction: column; align-items: center; justify-content: center;
    gap: 22px;
  }
  .front-mark {
    width: 70px; height: 70px; border-radius: 50%;
    background: var(--band);
  }
  .front-lockup .brand { text-align: center; }
  .front-lockup .brand__line { font-size: 40px; letter-spacing: 0.02em; }
  .front-lockup .brand__sub { font-size: 17px; margin-top: 6px; }

  /* back */
  .back-brand {
    position: absolute; top: 58px; right: 70px; text-align: center;
  }
  .back-brand .brand__line { font-size: 30px; letter-spacing: 0.02em; }
  .back-brand .brand__sub { font-size: 13px; margin-top: 5px; }

  .person {
    position: absolute; left: 78px; top: 168px;
  }
  .person__name {
    font-family: "Montserrat", sans-serif; font-weight: 700;
    font-size: 28px; color: var(--white); letter-spacing: 0.02em;
  }
  .person__title {
    font-family: "Questrial", sans-serif;
    font-size: 15px; color: var(--muted); margin-top: 4px;
  }

  .info-band {
    position: absolute; left: 0; right: 0; top: 245px; height: 112px;
    background: var(--band);
  }
  .band-mark {
    position: absolute; right: 70px; top: 205px;
    width: 170px; height: 170px; border-radius: 50%;
    background: var(--card-bg);
    border: 10px solid var(--band);
  }
  .contact {
    position: absolute; left: 120px; top: 262px;
    list-style: none;
    font-family: "Questrial", sans-serif; font-size: 20px; color: var(--white);
  }
  .contact__item { display: flex; align-items: center; gap: 12px; height: 27px; }
  .contact__icon {
    width: 17px; height: 17px; flex: none;
  }
</style>
</head>
<body>

<section class="card card--front">
  <div class="front-lockup">
    <div class="front-mark"></div>
    <div class="brand">
      <span class="brand__line">CrewSafe</span>
      <span class="brand__line brand__sub">Clinics</span>
    </div>
  </div>
</section>

<section class="card card--back">
  <div class="brand back-brand">
    <span class="brand__line">CrewSafe</span>
    <span class="brand__line brand__sub">Clinics</span>
  </div>

  <div class="person">
    <div class="person__name">DANIEL REYES</div>
    <div class="person__title">Executive Manage</div>
  </div>

  <div class="info-band"></div>
  <div class="band-mark"></div>

  <ul class="contact">
    <li class="contact__item">
      <svg class="contact__icon" viewBox="0 0 20 20"><circle cx="10" cy="10" r="10" fill="#fff"/><path d="M7 5.5l1.6 2.4-1 1c.6 1.3 1.5 2.2 2.8 2.8l1-1 2.4 1.6-.9 1.8c-3.6-.3-6.6-3.3-6.9-6.9z" fill="#85878a"/></svg>
      <span>555-010-777</span>
    </li>
    <li class="contact__item">
      <svg class="contact__icon" viewBox="0 0 20 20"><circle cx="10" cy="10" r="10" fill="#fff"/><rect x="5" y="6.5" width="10" height="7" fill="#85878a"/><path d="M5 6.5l5 4 5-4" fill="none" stroke="#fff" stroke-width="1"/></svg>
      <span>info@crewsafeclinics.com</span>
    </li>
    <li class="contact__item">
      <svg class="contact__icon" viewBox="0 0 20 20"><circle cx="10" cy="10" r="10" fill="#fff"/><path d="M10 5l5 4.5h-1.5V15h-7V9.5H5z" fill="#85878a"/></svg>
      <span>Your address, your city, box 88900</span>
    </li>
  </ul>
</section>

</body>
</html>
```